Private Investigation Business Card Design

I need a business card for a new private investigation company named Brisk Inquiries. I perform mainly surveillance jobs, vehicle repossessions, document serves etc. The final design should aim for a professional look. The logo has a magnifying glass with stick man arms and legs and is in a running action to show the "Brisk" aspect of the name. If the colour scheme could remain the same as the website www.briskinquiries-demo.com.au with silvers,blacks and a couple electric blue highlights.
Industry/Entity Type
Business
Contact Information for Business Card
Morgan Kellaway
Brisk Inquiries
0487316204
PO Box 58, Carnwell NSW 2291
info@briskinquiries-demo.com.au
www.briskinquiries-demo.com.au
Look and feel

```html
<!DOCTYPE html>
<html lang="en">
<head>
<meta charset="utf-8">
<title>Brisk Inquiries – Business Card</title>
<link rel="stylesheet" href="https://fonts.googleapis.com/css2?family=Arimo:wght@400;700&display=swap">
<style>
  :root {
    --backdrop: #2b2c2f;
    --silver-light: #d9d9db;
    --silver-mid: #a9a9ac;
    --silver-dark: #7d7d81;
    --white: #ffffff;
    --ink: #1a1a1a;
    --panel-black: #1f1f21;
    --text-grey: #3a3a3c;
  }
  * { margin: 0; padding: 0; box-sizing: border-box; }
  html, body {
    width: 1200px; height: 871px; overflow: hidden;
    background: var(--backdrop);
    font-family: "Arimo", Arial, sans-serif;
  }
  .stage {
    width: 1200px; height: 871px;
    display: flex; flex-direction: column; align-items: center; justify-content: center;
    gap: 40px;
  }
  .card {
    position: relative;
    width: 620px; height: 378px;
    overflow: hidden;
    box-shadow: 0 10px 30px rgba(0,0,0,.45);
  }

  /* Back of card */
  .card-back {
    background: linear-gradient(135deg, var(--silver-light) 0%, var(--silver-mid) 55%, var(--silver-dark) 100%);
  }
  .back-mark {
    position: absolute; left: 0; right: 0; top: 120px;
    display: flex; align-items: center; justify-content: center; gap: 14px;
  }
  .mark-dot {
    width: 26px; height: 26px; border-radius: 50%;
    background: var(--ink);
  }
  .back-name {
    font-size: 40px; font-weight: 700; color: var(--ink);
  }
  .back-url {
    position: absolute; left: 0; right: 0; bottom: 58px;
    text-align: center;
    font-size: 17px; letter-spacing: 2px; color: var(--text-grey);
  }

  /* Front of card */
  .card-front { background: var(--white); }
  .front-top {
    position: absolute; left: 0; top: 0; width: 100%; height: 170px;
    background: linear-gradient(180deg, #ffffff 0%, #f1f1f2 100%);
  }
  .front-logo {
    position: absolute; left: 26px; top: 52px;
    display: flex; align-items: center; gap: 12px;
  }
  .front-logo .mark-dot { width: 20px; height: 20px; background: var(--silver-dark); }
  .front-logo-name {
    font-size: 36px; font-weight: 700; color: var(--silver-dark);
  }
  .front-bottom {
    position: absolute; left: 0; top: 170px; width: 100%; height: 208px;
    background: linear-gradient(90deg, #c4c4c6 0%, #b3b3b6 50%, #9e9ea1 100%);
  }
  .contact {
    position: absolute; left: 26px; top: 190px;
    font-size: 15px; line-height: 1.45; color: var(--text-grey);
    list-style: none;
  }
  .contact .address { margin-bottom: 6px; }
  .contact li { display: flex; align-items: center; gap: 8px; }
  .contact svg { width: 14px; height: 14px; flex: none; }
  .address-line { padding-left: 0; }
  .dark-panel {
    position: absolute; left: 0; top: 0; width: 620px; height: 378px;
  }
  .runner-area {
    position: absolute; left: 348px; top: 200px;
    width: 68px; height: 68px; border-radius: 50%;
    background: radial-gradient(circle at 40% 35%, #f4f4f5 0%, #c9c9cc 70%, #9a9a9d 100%);
  }
  .holder-name {
    position: absolute; right: 30px; bottom: 30px;
    font-size: 21px; font-weight: 700; color: var(--white);
  }
</style>
</head>
<body>
<main class="stage">

  <section class="card card-back" aria-label="Card back">
    <div class="back-mark">
      <span class="mark-dot"></span>
      <span class="back-name">Brisk Inquiries</span>
    </div>
    <p class="back-url">www.briskinquiries-demo.com.au</p>
  </section>

  <section class="card card-front" aria-label="Card front">
    <div class="front-top"></div>
    <div class="front-bottom"></div>

    <svg class="dark-panel" viewBox="0 0 620 378" aria-hidden="true">
      <polygon points="360,230 400,170 620,170 620,378 360,378" fill="var(--panel-black)"/>
    </svg>

    <div class="front-logo">
      <span class="front-logo-name">Brisk Inquiries</span>
      <span class="mark-dot"></span>
    </div>

    <ul class="contact">
      <li class="address">PO Box 58<br>Carnwell NSW 2291</li>
      <li>
        <svg viewBox="0 0 14 14"><path d="M3 1h2.5l1 3-1.5 1a7 7 0 0 0 4 4l1-1.5 3 1V11a2 2 0 0 1-2 2A11 11 0 0 1 1 3a2 2 0 0 1 2-2z" fill="var(--text-grey)"/></svg>
        0487 316 204
      </li>
      <li>
        <svg viewBox="0 0 14 14"><rect x="1" y="3" width="12" height="8" fill="var(--text-grey)"/><path d="M1 3l6 5 6-5" fill="none" stroke="#c4c4c6" stroke-width="1"/></svg>
        info@briskinquiries-demo.com.au
      </li>
      <li>
        <svg viewBox="0 0 14 14"><circle cx="7" cy="7" r="6" fill="var(--text-grey)"/><path d="M1 7h12M7 1c-3 3-3 9 0 12M7 1c3 3 3 9 0 12" fill="none" stroke="#c4c4c6" stroke-width="0.8"/></svg>
        www.briskinquiries-demo.com.au
      </li>
    </ul>

    <div class="runner-area" role="img" aria-label="Brand emblem area"></div>

    <p class="holder-name">Morgan Kellaway</p>
  </section>

</main>
</body>
</html>
```